wardrobe/costume stylist needs good business card for own business

Hi:)

I'm wanting a business card for my company. I am a freelance stylist.

I do wardrobe/costume stylist to TV commercials; Films; Fashion and Lifestyle shoots.

I'd like a design based around my name Rosalind Parfrey written nicely, maybe a colour? Up to you?!

I've attached a couple of images of business cards I like
.... be creative and have fun!

Thank you :)

Reason: I was trying to get my new business card ready for before I headed overseas Friday morning but I don't think that was realistic so I'd like to extend the deadline to give time to the project. Thank you

Hi designers:) Thank you for all your designs, I've extended the deadline until Sunday, so there's a bit more time. I've attached 3 pictures of business cards which I quite like, please take a look to see if it can be of help in your process. I like the pale plain or patterned background with dark font and the dark plain or patterned background with the pale font the motifs the feminine fonts the plain fonts I like the idea of playing with a circle or some shape on one side of the card with my name or initials as in the picture I have on my post could you play around with this idea a bit please? Thank you all for the work you've done :) Rosa

Hi I am working overseas til Saturday night sorry for no feedback until I teturn Thanks :) Rosa

Hi designers, Thank you all so much for submitting your designs, I really appreciate your input into my project :) I'm sorry I didn't get to respond to some comments, and give feedback. I didn't back from being away until later than I expected, and the deadline had passed then, so apologies. Thanks to you all again for all your really good designs :) Rosa

Target Market(s)

I am a freelance stylist my target audience is producers, production companies, photographers, directors...

Industry/Entity Type

Business

Requirements
Must have
• Rosalind Parfrey
Stylist or Wardrobe Stylist

email rosaparfrey@mailbox-example.co.nz
Mobile 0218467193

(Don't have to use the words 'email' and 'mobile')
Nice to have
• Would like it to be double sided
Like B & W
Like pale colour background with dark font or white font
Like dark colour background with pale font
Should not have
• I would prefer it not to incorporate pictures

```html
<!DOCTYPE html>
<html lang="en">
<head>
<meta charset="utf-8">
<title>Rosalind Parfrey – Business Card</title>
<link rel="stylesheet" href="https://fonts.googleapis.com/css2?family=Italiana&family=Cormorant+Garamond:wght@500&family=Open+Sans:wght@400&display=swap">
<style>
  :root {
    --backdrop: #2e2e2e;
    --magenta: #ff0066;
    --blush: #ffd3e0;
    --cream: #fdf0e4;
    --ink: #555049;
    --rule: #8a847d;
  }
  * { margin: 0; padding: 0; box-sizing: border-box; }
  html, body {
    width: 1200px;
    height: 655px;
    overflow: hidden;
    background: var(--backdrop);
  }
  .card-spread {
    position: absolute;
    left: 207px;
    top: 213px;
    width: 785px;
    height: 228px;
    display: flex;
  }
  .card-front {
    width: 393px;
    height: 100%;
    background: var(--magenta);
    display: flex;
    align-items: center;
    justify-content: center;
  }
  .monogram {
    font-family: "Italiana", serif;
    font-size: 104px;
    line-height: 1;
    color: var(--blush);
    letter-spacing: -2px;
    margin-top: 6px;
  }
  .card-back {
    width: 392px;
    height: 100%;
    background: var(--cream);
    position: relative;
    text-align: center;
  }
  .card-name {
    position: absolute;
    left: 0;
    right: 0;
    top: 90px;
    font-family: "Italiana", serif;
    font-size: 40px;
    line-height: 1;
    color: var(--magenta);
    letter-spacing: 1px;
  }
  .card-role {
    position: absolute;
    left: 50px;
    right: 47px;
    top: 181px;
    display: flex;
    align-items: center;
    gap: 8px;
    font-family: "Cormorant Garamond", serif;
    font-weight: 500;
    font-size: 13px;
    color: var(--ink);
    letter-spacing: 0.3px;
    white-space: nowrap;
  }
  .card-role::before,
  .card-role::after {
    content: "";
    flex: 1;
    height: 1px;
    background: var(--rule);
  }
  .card-contact {
    position: absolute;
    left: 0;
    right: 0;
    top: 198px;
    font-family: "Open Sans", sans-serif;
    font-size: 10.5px;
    color: var(--ink);
  }
</style>
</head>
<body>
  <div class="card-spread">
    <section class="card-front">
      <span class="monogram">RP</span>
    </section>
    <section class="card-back">
      <h1 class="card-name">Rosalind Parfrey</h1>
      <p class="card-role">STYLIST OR WARDROBE STYLIST</p>
      <p class="card-contact">rosaparfrey@mailbox-example.co.nz | 0218467193</p>
    </section>
  </div>
</body>
</html>
```